Product Design for VelaMira

Design Brief for VelaMira Product Packaging

Objective:
Create a cohesive, elegant, and brand-consistent packaging design for the VelaMira product line. The signature visual theme should reflect luxury, femininity, and clean beauty values.

---

🎨 Core Design Direction

Unified Aesthetic: All containers must prominently feature the floral pattern shown in "Pattern Reference: Image 3". This design serves as the brand's signature aesthetic and must be applied uniformly across all SKUs.

Brand Logo Placement: The VelaMira logo (provided) should be clearly visible and harmoniously integrated into the patterned background.

Color Palette: Base colors should complement the brand’s primary palette: black, blush pink, and white.

---

🧴 Product-Specific Packaging Specifications

1. Mascara

Bottle Type: Sleek mascara tube with a wand applicator

Capacity: 5ml

Design: Use floral pattern from Pattern Reference Image 3. Ensure the pattern does not obstruct the readability of the logo or any regulatory text.

2. Eyebrow Growth Serum

Bottle Type: 5ml tube with fine-tip brush applicator

Capacity: 5ml

Design: Same floral pattern, scaled and applied proportionally to match the mascara for consistency

3. Eyelash Growth Serum

Bottle Type: 5ml tube with fine-tip brush (similar to the eyebrow serum, unless otherwise advised)

Capacity: 5ml

Design: Identical styling to maintain unity across lash & brow products

4. Anti-Aging Serum or Lotion

Bottle Type: 30ml airless pump bottle (preferred for hygiene and product stability)

Capacity: 30ml

Design: Apply floral pattern from Pattern Reference and scale appropriately for larger surface area

5. Hair Growth Spray

Bottle Type: 50ml fine mist spray bottle

Capacity: 50ml

Design: Pattern applied and scaled for taller profile; maintain visual harmony with skincare line

---

📦 Additional Notes

Please ensure packaging aligns with clean beauty standards (no overly glossy plastic finishes, avoid excessive secondary packaging unless sustainable).

Materials should be eco-conscious where possible.

If embossing, foil stamping, or UV finishing is available for logo accents, please suggest options.

```html
<!DOCTYPE html>
<html lang="en">
<head>
<meta charset="utf-8">
<title>VelaMira Hair Growth Spray Label</title>
<link href="https://fonts.googleapis.com/css2?family=Lato:wght@400;700&display=swap" rel="stylesheet">
<style>
  :root {
    --backdrop: #e6e7e8;
    --blush-light: #fcebe1;
    --blush-mid: #f6d3bf;
    --blush-deep: #f0bfa4;
    --panel: #ffffff;
    --ink: #1f1f1f;
    --coral: #ef8d67;
  }
  * { margin: 0; padding: 0; box-sizing: border-box; }
  html, body {
    width: 1200px; height: 1200px; overflow: hidden;
    background: var(--backdrop);
    font-family: "Lato", sans-serif;
    color: var(--ink);
  }
  .label {
    position: absolute; left: 50px; top: 145px;
    width: 1100px; height: 910px;
  }
  .floral-pattern {
    position: absolute; inset: 0;
    background:
      radial-gradient(circle at 20% 30%, var(--blush-mid) 0, transparent 35%),
      radial-gradient(circle at 75% 70%, var(--blush-mid) 0, transparent 40%),
      linear-gradient(135deg, var(--blush-light), var(--blush-deep));
  }
  .panel {
    position: absolute; background: var(--panel);
    display: flex; flex-direction: column; align-items: center;
    text-align: center;
  }
  .front-panel { left: 169px; top: 84px; width: 210px; height: 736px; }
  .back-panel { left: 717px; top: 107px; width: 214px; height: 700px; padding-top: 40px; }

  .brand-name-wrap {
    height: 470px; width: 100%;
    position: relative;
  }
  .brand-name {
    position: absolute; left: 50%; top: 50%;
    transform: translate(-50%, -50%) rotate(-90deg);
    font-size: 72px; font-weight: 400; letter-spacing: 1px;
    white-space: nowrap; line-height: 1;
  }
  .product-name { font-size: 31px; font-weight: 400; line-height: 1.22; margin-top: 18px; }
  .product-claim { font-size: 19px; line-height: 1.3; margin-top: 18px; }
  .product-volume { font-size: 19px; margin-top: 32px; }

  .info-block { font-size: 18px; line-height: 1.35; margin-bottom: 18px; padding: 0 10px; }
  .info-block h2 { font-size: 18px; font-weight: 700; }

  .badges {
    display: grid; grid-template-columns: 1fr 1fr; gap: 14px 20px;
    margin-top: 30px;
  }
  .badge { display: flex; flex-direction: column; align-items: center; width: 70px; }
  .badge svg { width: 48px; height: 48px; }
  .badge span { font-size: 9px; color: var(--coral); line-height: 1.15; margin-top: 3px; }

  .distributor { font-size: 17px; line-height: 1.45; margin-top: 38px; }
  .distributor strong { font-weight: 700; }
</style>
</head>
<body>
  <div class="label">
    <div class="floral-pattern" role="img" aria-label="Blush floral pattern of drawn blossoms and leaves"></div>

    <section class="panel front-panel">
      <div class="brand-name-wrap"><div class="brand-name">VelaMira</div></div>
      <h1 class="product-name">Hair Growth<br>Spray</h1>
      <p class="product-claim">Stimulates<br>+Strengthens</p>
      <p class="product-volume">50ml / 1.7 fl.oz.</p>
    </section>

    <section class="panel back-panel">
      <div class="info-block"><h2>Directions:</h2>Spray onto clean scalp. Gently massage. Use daily.</div>
      <div class="info-block"><h2>Ingredients:</h2>Aqua, Caffeine, Biotin, Ginseng Extract...</div>
      <div class="info-block"><h2>Caution:</h2>Avoid contact with eyes. For external use only.</div>

      <div class="badges">
        <div class="badge">
          <svg viewBox="0 0 48 48" fill="none" stroke="var(--coral)" stroke-width="1.6">
            <circle cx="24" cy="24" r="22"/>
            <path d="M20 13h8M21 13v9l-7 12h20l-7-12v-9"/>
            <path d="M12 12l24 24"/>
          </svg>
          <span>Paraben<br>Free</span>
        </div>
        <div class="badge">
          <svg viewBox="0 0 48 48" fill="none" stroke="var(--coral)" stroke-width="1.6">
            <circle cx="24" cy="24" r="22"/>
            <path d="M15 25l6 6 12-13"/>
          </svg>
          <span>Dermatologist<br>Tested</span>
        </div>
        <div class="badge">
          <svg viewBox="0 0 48 48" fill="none" stroke="var(--coral)" stroke-width="1.6">
            <circle cx="24" cy="24" r="22"/>
            <path d="M24 12c-5 7-8 11-8 15a8 8 0 0 0 16 0c0-4-3-8-8-15z"/>
          </svg>
          <span>Cruelty<br>Free</span>
        </div>
        <div class="badge">
          <svg viewBox="0 0 48 48" fill="none" stroke="var(--coral)" stroke-width="1.6">
            <circle cx="24" cy="24" r="22"/>
            <path d="M24 12c7 5 9 10 9 14a9 9 0 0 1-18 0c0-4 2-9 9-14z"/>
            <path d="M24 18v18M24 26l4-4M24 30l-4-4"/>
          </svg>
          <span>Strengthens<br>Roots</span>
        </div>
      </div>

      <p class="distributor">Distributed by<br><strong>VelaMira</strong>,<br>London, UK<br>velamirabeauty.com</p>
    </section>
  </div>
</body>
</html>
```